W. Darrow Billboard

2 miles ahead on right
Voted number 1 ... again!
California cuisine
Located in Historic Marbury Hill Inn
Picture of a couple dining
www.torvellis.com 555.317.2968

Target Market(s)

travelers

Industry/Entity Type

hospitality

Font styles to use
Serif

Colors
59FF00
82FF00
B8FF75
E3FFCB
F4FFEA
EE7325
F08F49
F5BC92
FAE3D3
FDF4ED

Requirements
Should not have
• bright colors

```html
<!DOCTYPE html>
<html lang="en">
<head>
<meta charset="utf-8">
<title>Torvelli's Billboard</title>
<link rel="stylesheet" href="https://fonts.googleapis.com/css2?family=Alfa+Slab+One&family=Federo&family=Zilla+Slab:wght@600;700&family=Roboto+Slab:wght@700&display=swap">
<style>
  :root {
    --page: #e6e9ec;
    --cream: #f4ffea;
    --cream-deep: #e3ffcb;
    --orange: #e2531f;
    --red: #c8201c;
    --green: #6fb81a;
    --green-dark: #3f7d12;
    --green-soft: #b8ff75;
    --gold: #ffd84a;
    --gray: #8a8a8a;
    --gray-light: #cfcfcf;
  }
  * { margin: 0; padding: 0; box-sizing: border-box; }
  html, body { width: 1200px; height: 800px; overflow: hidden; background: var(--page); }
  .billboard {
    position: absolute; left: 30px; top: 110px; width: 1140px; height: 580px;
    background: linear-gradient(160deg, var(--cream) 0%, #f7faef 60%, var(--cream-deep) 100%);
    overflow: hidden; box-shadow: 0 6px 20px rgba(0,0,0,.18);
  }
  .corner-bands { position: absolute; inset: 0; width: 100%; height: 100%; }
  .brand { position: absolute; left: 50px; top: 24px; color: var(--orange); }
  .brand-name {
    font-family: "Alfa Slab One", serif; font-size: 112px; line-height: 1; letter-spacing: 1px;
  }
  .brand-sub {
    font-family: "Zilla Slab", serif; font-weight: 700; font-size: 30px; letter-spacing: 8px;
    margin: 4px 0 0 120px; line-height: 1.05; text-transform: uppercase;
  }
  .brand-sub small { display: block; font-size: 22px; letter-spacing: 6px; margin-left: 70px; }
  .lime-art {
    position: absolute; left: 740px; top: 46px; width: 120px; height: 120px;
    border-radius: 50%; background: radial-gradient(circle, #d6f29a, #9fd23a);
  }
  .award {
    position: absolute; left: 880px; top: 40px; width: 200px; height: 118px;
    background: var(--red); color: #fff;
    clip-path: polygon(12% 0, 100% 0, 100% 78%, 88% 100%, 0 100%, 0 22%);
    display: flex; align-items: center; padding-left: 18px; gap: 10px;
  }
  .award-num { font-family: "Alfa Slab One", serif; font-size: 72px; line-height: 1; }
  .award-text { font-family: "Roboto Slab", serif; font-weight: 700; font-size: 17px; line-height: 1.2; }
  .award-text em { font-style: normal; color: var(--gold); font-size: 26px; display: block; }
  .award-stars { color: var(--green-soft); font-size: 12px; letter-spacing: 2px; }
  .tagline {
    position: absolute; left: 640px; top: 186px;
    font-family: "Federo", serif; font-size: 44px; line-height: 1; color: var(--green);
    -webkit-text-stroke: 1px var(--green-dark);
  }
  .cuisine {
    position: absolute; left: 60px; top: 238px;
    font-family: "Alfa Slab One", serif; font-size: 78px; line-height: 1; color: var(--green);
    text-shadow: 3px 3px 0 #fff, -3px -3px 0 #fff, 3px -3px 0 #fff, -3px 3px 0 #fff, 5px 6px 8px rgba(0,0,0,.25);
  }
  .venue {
    position: absolute; left: 150px; top: 336px;
    font-family: "Zilla Slab", serif; font-weight: 600; font-size: 36px; line-height: 1; color: var(--gray);
  }
  .contact {
    position: absolute; left: 95px; top: 398px;
    font-family: "Alfa Slab One", serif; font-size: 42px; color: var(--green); line-height: 1.25;
  }
  .contact .web { display: block; margin-left: 230px; }
  .dining-photo {
    position: absolute; left: 840px; top: 300px; width: 260px; height: 240px;
    border: 6px solid #fff; outline: 3px solid var(--green);
    background: linear-gradient(135deg, #2f4a55, #6e5a4a 55%, #b33a36);
  }
</style>
</head>
<body>
  <main class="billboard">
    <svg class="corner-bands" viewBox="0 0 1140 580" preserveAspectRatio="none" aria-hidden="true">
      <polygon points="0,400 0,580 180,580" fill="var(--gray-light)"/>
      <polygon points="0,440 0,580 140,580" fill="var(--green)"/>
      <polygon points="0,500 0,580 80,580" fill="var(--red)"/>
      <polygon points="1140,0 960,0 1140,250" fill="var(--gray-light)"/>
      <polygon points="1140,0 1010,0 1140,190" fill="var(--green)"/>
      <polygon points="1140,0 1060,0 1140,110" fill="var(--red)"/>
    </svg>

    <div class="brand">
      <div class="brand-name">Torvelli's</div>
      <div class="brand-sub">Southwest<small>Bar &amp; Grill</small></div>
    </div>
    <div class="lime-art" role="img" aria-label="Lime slice illustration"></div>

    <div class="award">
      <span class="award-num">1</span>
      <div class="award-text">Voted Number<em>again!</em><span class="award-stars">★★★★★</span></div>
    </div>

    <div class="tagline">Good Food, Good Life</div>
    <div class="cuisine">California Cuisine</div>
    <div class="venue">Historic Marbury Hill Inn</div>
    <div class="contact">555.317.2968<span class="web">www.torvellis.com</span></div>

    <div class="dining-photo" role="img" aria-label="Photo of a couple dining together at a restaurant table"></div>
  </main>
</body>
</html>
```